Corvel Capital LLC

Need Professional Business cards for New Investment Fund

Target Market(s)

High Quality investors

Industry/Entity Type

Financial

Contact Information for Business Card

Phone Number +1 555 284 6190
Name Lukas Varenko
Title Fund Manager
email lv@FundCorvel.com
Website www.FundCorvel.com

Colors

Designer to choose colors to be used in the design.

Requirements
Must have
• Must have our Logo and all of the above. Must be made so lettering and loge can be raised

```html
<!DOCTYPE html>
<html lang="en">
<head>
<meta charset="utf-8">
<title>Talvenor – Business Card</title>
<link rel="stylesheet" href="https://fonts.googleapis.com/css2?family=Jost:wght@500&family=Lato:wght@400&display=swap">
<style>
  :root {
    --backdrop: #2a2b2d;
    --card-dark: #1b1c1e;
    --card-olive: #414d3f;
    --accent-green: #23e012;
    --text-light: #f2f2f2;
    --rule-grey: #8c948a;
    --pattern-tone: #26282a;
  }
  * { box-sizing: border-box; margin: 0; padding: 0; }
  html, body { width: 1200px; height: 1108px; overflow: hidden; }
  body {
    background: var(--backdrop);
    font-family: "Lato", sans-serif;
    position: relative;
  }
  .card {
    position: absolute;
    top: 204px;
    width: 400px;
    height: 700px;
    border-radius: 24px;
    overflow: hidden;
    background: var(--card-dark);
    box-shadow: 0 14px 30px rgba(0,0,0,0.45);
  }
  .card--front { left: 170px; }
  .card--back { left: 630px; }

  .front-shape { position: absolute; inset: 0; }

  .brand-name {
    position: absolute;
    left: 0; right: 0;
    top: 150px;
    text-align: center;
    font-family: "Jost", sans-serif;
    font-weight: 500;
    font-size: 44px;
    letter-spacing: 2px;
    color: var(--accent-green);
  }

  .contact-block {
    position: absolute;
    left: 0; right: 0;
    top: 418px;
    text-align: center;
    color: var(--text-light);
  }
  .person-name {
    font-family: "Jost", sans-serif;
    font-weight: 500;
    font-size: 29px;
    letter-spacing: 0.5px;
    text-transform: uppercase;
    color: var(--accent-green);
  }
  .person-title {
    font-size: 21px;
    margin-top: 2px;
  }
  .icon-row {
    display: flex;
    align-items: center;
    justify-content: center;
    gap: 6px;
    margin: 12px auto 12px;
    width: 300px;
  }
  .icon-row .rule {
    flex: 1;
    height: 1px;
    background: var(--rule-grey);
  }
  .icon-row svg { width: 26px; height: 26px; }
  .contact-line {
    font-size: 21px;
    line-height: 30px;
  }

  .back-pattern {
    position: absolute;
    inset: 0;
    background: linear-gradient(160deg, var(--pattern-tone) 0%, var(--card-dark) 75%);
  }
  .back-brand {
    position: absolute;
    right: 60px;
    top: 438px;
    font-family: "Jost", sans-serif;
    font-weight: 500;
    font-size: 28px;
    letter-spacing: 1px;
    color: var(--accent-green);
  }
</style>
</head>
<body>

  <section class="card card--front" aria-label="Business card front">
    <svg class="front-shape" viewBox="0 0 400 700" aria-hidden="true">
      <path d="M0 318 Q200 250 400 338 L400 700 L0 700 Z" fill="var(--card-olive)"/>
      <path d="M0 318 Q200 250 400 338" fill="none" stroke="var(--accent-green)" stroke-width="6"/>
    </svg>

    <div class="brand-name">Talvenor</div>

    <div class="contact-block">
      <div class="person-name">Lukas Varenko</div>
      <div class="person-title">Fund Manager</div>

      <div class="icon-row">
        <span class="rule"></span>
        <svg viewBox="0 0 26 26" aria-label="Phone">
          <circle cx="13" cy="13" r="12" fill="var(--accent-green)"/>
          <path d="M8.5 7.5 L11 7.5 L12 10.5 L10.5 11.5 Q12 14.5 14.5 15.5 L15.5 14 L18.5 15 L18.5 17.5 Q12 19 8.5 12 Z" fill="var(--card-olive)"/>
        </svg>
        <svg viewBox="0 0 26 26" aria-label="Email">
          <circle cx="13" cy="13" r="12" fill="var(--accent-green)"/>
          <rect x="7" y="9" width="12" height="8.5" fill="var(--card-olive)"/>
          <path d="M7 9 L13 14 L19 9" fill="none" stroke="var(--accent-green)" stroke-width="1.2"/>
        </svg>
        <svg viewBox="0 0 26 26" aria-label="Website">
          <circle cx="13" cy="13" r="12" fill="var(--accent-green)"/>
          <circle cx="13" cy="13" r="6.5" fill="none" stroke="var(--card-olive)" stroke-width="1.6"/>
          <ellipse cx="13" cy="13" rx="2.8" ry="6.5" fill="none" stroke="var(--card-olive)" stroke-width="1.3"/>
          <line x1="6.5" y1="13" x2="19.5" y2="13" stroke="var(--card-olive)" stroke-width="1.3"/>
        </svg>
        <span class="rule"></span>
      </div>

      <div class="contact-line">+1 555 284 6190</div>
      <div class="contact-line">lv@FundCorvel.com</div>
      <div class="contact-line">www.FundCorvel.com</div>
    </div>
  </section>

  <section class="card card--back" aria-label="Business card back">
    <div class="back-pattern" role="img" aria-label="Faint repeating brand pattern in dark grey tones"></div>
    <div class="back-brand">Talvenor</div>
  </section>

</body>
</html>
```